Bluefinch Painting needs a Website

We need a website built for a Painting company I own, we mainly do residential painting, but don't want to be limited to that.

Need to have estimate request form.
Need pic's of past projects

I like the look of the website for http://www.harbor-brushworks.com
& "Westlake Home inspections"

My logo that was designed here on ArtHatch on the front page

I would like one of the houses I downloaded as part of the background
of the front page.

Target Market(s)

Home owners

Industry/Entity Type

Painting

Number of Pages Required

1 page

Font styles to use
Serif

Requirements
Must have
• Estimate request form for home owners to fill out -
• Name:
• Phone Number:
• Address:
• E-mail:
• Painting project description:
• And my info to:
• My phone number: (555) 318-7046
• My web address bluefinchpainting.example
Nice to have
• My logo that was designed here on ArtHatch

```html
<!DOCTYPE html>
<html lang="en">
<head>
<meta charset="utf-8">
<title>Bluefinch Painting</title>
<link href="https://fonts.googleapis.com/css2?family=Roboto+Slab:wght@400;700&family=Vollkorn:wght@400&family=Arimo:wght@400;700&display=swap" rel="stylesheet">
<style>
:root{
  --blue:#1c7ccc;
  --blue-dark:#1669b0;
  --ink:#222;
  --panel:#f2f2f2;
  --dark:#262a2c;
  --white:#fff;
  --field:#d9dbdc;
}
*{box-sizing:border-box;margin:0;padding:0}
html,body{width:1188px;height:1200px;overflow:hidden;background:var(--white)}
body{position:relative;font-family:Arimo,Arial,sans-serif;color:var(--ink)}
.abs{position:absolute}

/* header */
.brand{left:158px;top:40px;display:flex;align-items:center;gap:10px;font-family:Vollkorn,serif;font-size:31px;color:var(--ink);letter-spacing:1px}
.brand-mark{width:26px;height:26px;background:var(--blue)}
.cta{left:712px;top:17px;width:148px;height:28px;background:var(--blue);color:var(--white);font-size:17px;text-align:center;line-height:28px}
.call{left:875px;top:13px;display:flex;gap:8px;align-items:center}
.call small{display:block;font-size:14px}
.call strong{display:block;font-size:19px;font-weight:400}
.nav{left:585px;top:70px;display:flex;gap:20px;font-size:13px;align-items:center}
.nav a{color:var(--ink);text-decoration:none;line-height:24px}
.nav .active{background:var(--blue);color:var(--white);padding:0 14px}

/* hero */
.hero{left:0;top:114px;width:1188px;height:394px;background:linear-gradient(180deg,#8fb4dc 0%,#b9cbdc 25%,#9c917c 45%,#7d7566 62%,#4d7a3e 80%,#3e6a31 100%)}
.hero h1{position:absolute;right:167px;top:76px;text-align:right;font-family:"Roboto Slab",serif;font-weight:400;font-size:31px;line-height:37px;color:var(--white)}
.arrow{top:180px;width:34px;height:30px;background:rgba(40,40,40,.75)}
.tab{top:463px;height:45px;font-family:"Roboto Slab",serif;font-size:20px;color:var(--white);line-height:52px;padding:0 12px}
.tab.res{left:158px;width:244px;background:var(--blue);font-weight:700}
.tab.com{left:428px;width:244px;background:#2c2c2c}

/* projects */
.projects{left:158px;top:508px;width:873px;height:213px;background:var(--panel)}
.filter{left:178px;top:526px;font-family:Vollkorn,serif;font-size:19px}
.filter .sep{display:inline-block;width:1px;height:20px;background:var(--blue);margin:0 8px;vertical-align:-3px}
.filter .on{color:var(--blue)}
.thumb{top:568px;width:153px;height:122px;border:1px solid #444;background:var(--white);padding:4px}
.thumb .pic{position:relative;width:100%;height:100%}
.thumb span{position:absolute;left:0;right:0;bottom:0;height:22px;background:rgba(0,0,0,.5);color:var(--white);font-family:Vollkorn,serif;font-size:15px;padding-left:8px;line-height:22px}

/* about + form */
.band{left:0;top:766px;width:1188px;height:365px;background:linear-gradient(180deg,#2e3236,#232628 60%,#2a2c2e)}
.title{font-family:Vollkorn,serif;font-size:22px;color:var(--white)}
.rule{height:5px;border-top:1px solid #ddd;border-bottom:1px solid #ddd}
.copy{left:161px;top:845px;width:510px;font-size:12.5px;line-height:22px;color:var(--white)}
.btn{height:27px;border:2px solid #ddd;border-radius:3px;color:var(--white);font-size:13px;font-weight:700;text-align:center;line-height:23px}
.field{left:730px;width:260px;height:29px;background:var(--field);color:#333;font-size:12.5px;padding:6px 11px;border-radius:2px}

/* footer */
.footer{left:0;top:1133px;width:1188px;height:67px;background:var(--blue);color:var(--white)}
.footer .links{position:absolute;left:163px;top:14px;display:flex;gap:18px;font-size:13px}
.footer .copy-line{position:absolute;left:160px;top:36px;font-size:12px}
.footer .brand{left:805px;top:18px;color:var(--white);font-size:22px}
.footer .brand-mark{width:18px;height:18px;background:var(--white)}
</style>
</head>
<body>
<header>
  <div class="abs brand"><span class="brand-mark"></span>BLUEFINCH PAINTING</div>
  <div class="abs cta">Free Estimates</div>
  <div class="abs call">
    <svg width="28" height="28" viewBox="0 0 28 28" aria-hidden="true"><circle cx="14" cy="14" r="12.5" fill="none" stroke="#1c7ccc" stroke-width="2"/><path d="M10 8c-2 2-1 7 3 11s8 4 9 2l-3-3-2 1c-2-1-4-3-5-5l1-2z" fill="#1c7ccc"/></svg>
    <div><small>Call Us Today</small><strong>(555) 318-7046</strong></div>
  </div>
  <nav class="abs nav">
    <a class="active">HOME</a><a>ABOUT US</a><a>SERVICES</a><a>PAST PROJECTS</a><a>CONTACT US</a>
  </nav>
</header>

<section class="abs hero" role="img" aria-label="Two-storey beige house with flowering garden under blue sky">
  <h1>PROVIDING QUALITY WORK AT<br>AFFORDABLE PRICES</h1>
  <svg class="abs arrow" style="left:6px" viewBox="0 0 34 30" aria-hidden="true"><path d="M19 9l-6 6 6 6" stroke="#fff" stroke-width="2.5" fill="none"/></svg>
  <svg class="abs arrow" style="right:6px" viewBox="0 0 34 30" aria-hidden="true"><path d="M15 9l6 6-6 6" stroke="#fff" stroke-width="2.5" fill="none"/></svg>
</section>
<div class="abs tab res">RESIDENTIAL PAINTING</div>
<div class="abs tab com">COMMERCIAL PAINTING</div>

<section class="abs projects"></section>
<div class="abs filter">Interior<span class="sep"></span><span class="on">Exterior</span></div>
<div class="abs thumb" style="left:173px"><div class="pic" role="img" aria-label="Painted house with garden" style="background:linear-gradient(180deg,#6f9fd4,#8a8068 50%,#4f7a3c)"><span>Lorem Ispum</span></div></div>
<div class="abs thumb" style="left:344px"><div class="pic" role="img" aria-label="Painter working on white siding gable" style="background:linear-gradient(180deg,#2f6dbd,#d5d8dc 50%,#b9bcc0)"><span>Lorem Ispum</span></div></div>
<div class="abs thumb" style="left:515px"><div class="pic" role="img" aria-label="Painter spraying yellow wall" style="background:linear-gradient(180deg,#d8c98e,#e6dfc8 60%,#c8b680)"><span>Lorem Ispum</span></div></div>
<div class="abs thumb" style="left:686px"><div class="pic" role="img" aria-label="Beige house with green lawn" style="background:linear-gradient(180deg,#9cc3e6,#b9a98a 50%,#4d8a3a)"><span>Lorem Ispum</span></div></div>
<div class="abs thumb" style="left:857px"><div class="pic" role="img" aria-label="Grey house with patio" style="background:linear-gradient(180deg,#aab0b2,#7d7b72 55%,#4f5a46)"><span>Lorem Ispum</span></div></div>

<section class="abs band" role="img" aria-label="Company work trucks parked in front of a house, darkened"></section>
<div class="abs title" style="left:161px;top:790px">Welcome to Bluefinch Painting</div>
<div class="abs rule" style="left:161px;top:823px;width:341px"></div>
<p class="abs copy">Lorem ipsum dolor sit amet, consectetuer adipiscing elit, sed diam nonummy nibh euismod consequat. Duis autem revel eum iriure dolor in hendrerit in vulputate velit esse molestie consequat.Lorem ipsum dolor sit amet, consectetuer adipiscing elit, sed diam nonummy nibh euismod rent ut laoreet dolore magna aliquam erat volutpat. Ut wisi enim ad minim veniam, quis nostrud lore xererci tation ullamcorper suscipit lobortis nisl ut aliquip ex ea commodo consequat. Duis autem revel eum iriure dolor in hendrerit in vulputate velit esse molestie consequat.nibh euismod rent ut laoreet dolore magna aliquam erat volutpat. Ut wisi enim ad minim veniam, quis nostrud lore xererci tation ullamcorper suscipit lobortis nisl ut aliquip ex ea commodo consequat.</p>
<div class="abs btn" style="left:158px;top:1054px;width:87px">Read More</div>

<div class="abs title" style="left:729px;top:788px">Free Painting Estimates</div>
<div class="abs rule" style="left:729px;top:823px;width:302px"></div>
<div class="abs field" style="top:851px">Name</div>
<div class="abs field" style="top:890px">Email</div>
<div class="abs field" style="top:929px">Phone</div>
<div class="abs field" style="top:968px;height:75px">Painting project description</div>
<div class="abs btn" style="left:730px;top:1054px;width:87px">Submit</div>

<footer class="abs footer">
  <div class="links"><span>• Home</span><span>• About Us</span><span>• Services</span><span>• Past Projects</span><span>• Contact Us</span></div>
  <div class="copy-line">Copyright ©2015, BluefinchPainting  All Rights Reserved</div>
  <div class="abs brand"><span class="brand-mark"></span>BLUEFINCH PAINTING</div>
</footer>
</body>
</html>
```